Tech Company New PowerPoint Design Project

We are an IT Managed services, cloud and cyber security company https://www.travolin.com.au/ Requesting proposals for a PowerPoint deck template that can be used by our sales team when pitching clients, our head office is located in Australa and we do have regional offices in NZ , USA , SRI LANKA and SINGAPORE. and also required to have a proposal/SOW template created too (not sure if this is something that we can include to this proposal) we may need a lot of things done in future but this is where i like to get started for now.. please let m eknow your thoughts and if you have any questions.
Target Market(s)
Enterprise
Industry/Entity Type
Information Technology
Look and feel

```html
<!DOCTYPE html>
<html lang="en">
<head>
<meta charset="utf-8">
<title>Travolin – Sales Deck</title>
<link href="https://fonts.googleapis.com/css2?family=Open+Sans:wght@400;600&family=Rubik:wght@700&display=swap" rel="stylesheet">
<style>
  :root{
    --sky:#29b6e8;
    --sky-deep:#1a9fdb;
    --sky-pale:#eaf6fc;
    --ink:#4a4f55;
    --ink-soft:#6b7076;
    --title:#555a60;
    --muted:#8c9196;
    --grey-hex:#6e7378;
    --night:#0b2a4a;
    --white:#ffffff;
  }
  *{box-sizing:border-box;margin:0;padding:0}
  html,body{width:1200px;height:4147px;overflow:hidden}
  body{
    background:linear-gradient(180deg,#5cc9f1 0%,#6fb2d6 45%,#7c8c98 100%);
    font-family:"Open Sans",Arial,sans-serif;color:var(--ink);
    position:relative;
  }
  .slide{position:absolute;left:44px;width:1112px;height:625px;background:var(--white);overflow:hidden;box-shadow:0 2px 8px rgba(0,0,0,.15)}
  .s1{top:55px}.s2{top:735px}.s3{top:1413px}.s4{top:2092px}.s5{top:2771px}.s6{top:3450px}
  .abs{position:absolute}
  .brand{font-family:"Open Sans",Arial,sans-serif;font-weight:400;color:var(--sky);letter-spacing:1px;line-height:1}
  .brand-corner{position:absolute;right:30px;top:26px;font-size:30px}
  .title{position:absolute;left:30px;top:26px;font-family:"Rubik",Arial,sans-serif;font-weight:700;font-size:40px;color:var(--title);letter-spacing:.5px}
  .footer-url,.footer-page{position:absolute;bottom:18px;font-size:12.5px;color:var(--muted)}
  .footer-url{left:30px}
  .footer-page{right:30px}
  .footer-page b{color:var(--sky);font-weight:400}
  .body-text{font-size:15px;line-height:32px;color:var(--ink)}

  /* cover + closing */
  .hero{position:absolute;left:0;top:0}
  .cover-brand{position:absolute;left:30px;font-size:66px}
  .divider{position:absolute;width:1px;background:#9aa0a6}
  .cover-copy{position:absolute;left:372px;top:475px;width:690px;font-size:14.5px;line-height:27px;color:var(--ink)}
  .regions{position:absolute;left:372px;top:568px;display:flex;gap:14px;align-items:center;font-size:14.5px;color:var(--ink)}
  .regions .dot{width:6px;height:6px;border-radius:50%;background:var(--sky)}
  .thanks{position:absolute;left:460px;top:502px;font-family:"Rubik",Arial,sans-serif;font-weight:700;font-size:31px;color:var(--muted);letter-spacing:.5px}
  .site{position:absolute;left:460px;top:550px;display:flex;align-items:center;gap:10px;font-size:20px;color:var(--ink)}

  /* passion */
  .passion-title{left:540px;top:228px;font-family:"Rubik",Arial,sans-serif;font-weight:700;font-size:40px;color:var(--title)}
  .passion-copy{left:540px;top:298px;width:545px;font-size:16px;line-height:31px}

  /* about */
  .about-copy{left:30px;top:126px;width:480px}
  .about-photo{left:30px;top:350px;width:470px;height:198px;border-radius:4px;background:linear-gradient(135deg,#3d3a36,#8a8175 45%,#cfd2d3 70%,#5a6168)}
  .about-list{left:565px;top:126px;width:520px;list-style:none}
  .about-list li{position:relative;padding-left:34px;margin-bottom:0}
  .about-list li::before{content:"";position:absolute;left:0;top:11px;width:11px;height:11px;border-radius:50%;background:var(--sky)}
  .about-band{left:230px;top:530px;width:470px;height:95px;background:var(--sky-pale)}

  /* services */
  .services-lead{left:30px;top:88px;width:1050px;font-size:15px;line-height:32px}
  .svc-map{left:0;top:0}
  .svc-label{font-family:"Open Sans",Arial,sans-serif;font-size:18px;fill:var(--ink)}

  /* partners */
  .partner-grid{left:0;top:0}
</style>
</head>
<body>

<!-- Slide 1: cover -->
<section class="slide s1">
  <svg class="hero" width="1112" height="460" viewBox="0 0 1112 460" role="img" aria-label="Photo of a data centre server aisle lit in blue and orange">
    <defs>
      <linearGradient id="serverGlow" x1="0" y1="0" x2="1" y2="0">
        <stop offset="0" stop-color="#0a1a30"/>
        <stop offset=".35" stop-color="#14335a"/>
        <stop offset=".7" stop-color="#1f6a9e"/>
        <stop offset="1" stop-color="#7fc9ec"/>
      </linearGradient>
    </defs>
    <path d="M0 318 C300 490 820 420 1112 175 V195 C820 445 300 510 0 338 Z" fill="var(--sky-deep)"/>
    <path d="M0 0 H1112 V160 C820 410 300 470 0 300 Z" fill="url(#serverGlow)"/>
  </svg>
  <div class="brand cover-brand" style="top:478px">travolin</div>
  <div class="divider" style="left:332px;top:468px;height:110px"></div>
  <p class="cover-copy">TRAVOLIN is a one-stop destination for all your IT Management Requirements. We are committed to delivering cutting-edge, simplified IT solutions through our highly skilled team and flexible engagement models.</p>
  <div class="regions"><span>NZ</span><span class="dot"></span><span>USA</span><span class="dot"></span><span>SRI LANKA</span><span class="dot"></span><span>SINGAPORE</span></div>
</section>

<!-- Slide 2: passion -->
<section class="slide s2">
  <svg class="hero" width="620" height="625" viewBox="0 0 620 625" role="img" aria-label="Photo of two colleagues studying a data dashboard">
    <defs>
      <linearGradient id="teamWarm" x1="0" y1="0" x2="1" y2="1">
        <stop offset="0" stop-color="#5a3a22"/>
        <stop offset=".45" stop-color="#b07a4c"/>
        <stop offset=".8" stop-color="#3a4a55"/>
        <stop offset="1" stop-color="#1d2a33"/>
      </linearGradient>
    </defs>
    <path d="M575 0 C555 300 400 525 0 592 V600 C410 535 566 300 588 0 Z" fill="var(--sky-deep)"/>
    <path d="M0 0 H562 C540 300 385 515 0 580 Z" fill="url(#teamWarm)"/>
  </svg>
  <div class="brand brand-corner">travolin</div>
  <h2 class="abs passion-title">OUR PASSION</h2>
  <p class="abs body-text passion-copy">Enthusiasm and value are what make us different from our peers. While there are many businesses providing the same services, what we deliver is unparalleled. Whether services or solutions, we keep standing with our clients through thick and thin.</p>
  <div class="footer-url">www.travolin.com.au</div>
  <div class="footer-page">Page: <b>2</b></div>
</section>

<!-- Slide 3: about -->
<section class="slide s3">
  <div class="abs about-band"></div>
  <h2 class="title">ABOUT US</h2>
  <div class="brand brand-corner">travolin</div>
  <p class="abs body-text about-copy">TRAVOLIN is a one-stop destination for all your IT Management Requirements. We are committed to delivering cutting-edge, simplified IT solutions through our highly skilled team and flexible engagement models. Whether you need support for integration or ongoing operational services, TRAVOLIN has the insight and technical capability to deliver simplified solutions.</p>
  <div class="abs about-photo" role="img" aria-label="Photo of a team meeting around a table in a bright office"></div>
  <ul class="abs body-text about-list">
    <li>Our passion, enthusiasm, and value are what make us different from our peers. While there are many businesses providing the same services, what we deliver is unparalleled. Whether services or solutions, we keep standing with our clients through thick and thin.</li>
    <li>Whether you need support for integration or ongoing operational services, TRAVOLIN has the insight and technical capability to deliver simplified solutions.</li>
    <li>Being an Australian based organization, we are 100% Customer Focused and provide innovative and flexible IT services and simple solutions that enhance business productivity. We pride ourselves on the flexibility in our approach.</li>
  </ul>
  <div class="footer-url">www.travolin.com.au</div>
  <div class="footer-page">Page: <b>3</b></div>
</section>

<!-- Slide 4: services -->
<section class="slide s4">
  <svg class="abs svc-map" width="1112" height="625" viewBox="0 0 1112 625">
    <defs>
      <polygon id="hexOuter" points="0,-40 34.6,-20 34.6,20 0,40 -34.6,20 -34.6,-20"/>
      <polygon id="hexInner" points="0,-32 27.7,-16 27.7,16 0,32 -27.7,16 -27.7,-16"/>
    </defs>
    <circle cx="565" cy="338" r="160" fill="none" stroke="#c9d3da" stroke-width="1.5" stroke-dasharray="3 5"/>
    <circle cx="565" cy="338" r="100" fill="#e4f2f9"/>
    <circle cx="565" cy="338" r="74" fill="var(--white)" stroke="var(--sky-deep)" stroke-width="4"/>
    <text x="565" y="350" text-anchor="middle" class="brand" font-size="30" fill="var(--sky)">travolin</text>

    <g transform="translate(445 221)"><use href="#hexOuter" fill="#bfe8f8"/><use href="#hexInner" fill="var(--sky)"/><circle cx="0" cy="-5" r="7" fill="none" stroke="#fff" stroke-width="2"/><path d="M-11 12 Q0 0 11 12" fill="none" stroke="#fff" stroke-width="2"/></g>
    <g transform="translate(685 221)"><use href="#hexOuter" fill="#bfe8f8"/><use href="#hexInner" fill="var(--sky)"/><circle cx="-3" cy="-3" r="8" fill="none" stroke="#fff" stroke-width="2"/><line x1="3" y1="3" x2="11" y2="11" stroke="#fff" stroke-width="2.5"/></g>
    <g transform="translate(393 342)"><use href="#hexOuter" fill="#d3d6d9"/><use href="#hexInner" fill="var(--grey-hex)"/><circle r="10" fill="none" stroke="#fff" stroke-width="2" stroke-dasharray="4 2.5"/><circle r="4" fill="none" stroke="#fff" stroke-width="2"/></g>
    <g transform="translate(736 342)"><use href="#hexOuter" fill="#d3d6d9"/><use href="#hexInner" fill="var(--grey-hex)"/><path d="M-11 -4 L0 -10 L11 -4 L0 2 Z M-11 2 L0 8 L11 2" fill="none" stroke="#fff" stroke-width="2"/></g>
    <g transform="translate(445 463)"><use href="#hexOuter" fill="#bfe8f8"/><use href="#hexInner" fill="var(--sky)"/><circle r="11" fill="none" stroke="#fff" stroke-width="2"/><ellipse rx="5" ry="11" fill="none" stroke="#fff" stroke-width="1.6"/><line x1="-11" x2="11" stroke="#fff" stroke-width="1.6"/></g>
    <g transform="translate(685 463)"><use href="#hexOuter" fill="#bfe8f8"/><use href="#hexInner" fill="var(--sky)"/><path d="M0 -11 L9 -7 V1 Q9 8 0 12 Q-9 8 -9 1 V-7 Z" fill="none" stroke="#fff" stroke-width="2"/><path d="M-4 0 L-1 3 L5 -4" fill="none" stroke="#fff" stroke-width="2"/></g>
    <g transform="translate(565 511)"><use href="#hexOuter" fill="#d3d6d9"/><use href="#hexInner" fill="var(--grey-hex)"/><circle r="11" fill="none" stroke="#fff" stroke-width="2"/><circle r="4" fill="#fff"/></g>

    <text x="375" y="227" text-anchor="end" class="svc-label">Service Desk</text>
    <text x="753" y="227" class="svc-label">Project Services</text>
    <text x="323" y="348" text-anchor="end" class="svc-label">Procurement Services</text>
    <text x="793" y="348" class="svc-label">Software Development</text>
    <text x="375" y="469" text-anchor="end" class="svc-label">Network Operations Center</text>
    <text x="753" y="469" class="svc-label">Security Operations Center</text>
    <text x="565" y="578" text-anchor="middle" class="svc-label">AI as a Service</text>
  </svg>
  <h2 class="title">SERVICES</h2>
  <div class="brand brand-corner">travolin</div>
  <p class="abs services-lead">Our support consists of great IT Services and a Passionate customer service TEAM to make sure you operate continuously without interruption</p>
  <div class="footer-url">www.travolin.com.au</div>
  <div class="footer-page">Page: <b>4</b></div>
</section>

<!-- Slide 5: partners -->
<section class="slide s5">
  <h2 class="title">OUR PARTNERS</h2>
  <div class="brand brand-corner">travolin</div>
  <svg class="abs partner-grid" width="1112" height="625" viewBox="0 0 1112 625" role="img" aria-label="Grid of partner badges">
    <g fill="#b9c0c6">
      <rect x="156" y="105" width="90" height="22" rx="3"/><rect x="366" y="105" width="142" height="22" rx="3"/><rect x="646" y="107" width="56" height="18" rx="3"/><rect x="882" y="103" width="52" height="26" rx="3"/>
      <rect x="126" y="165" width="150" height="34" rx="4" fill="#4a4f55"/><rect x="396" y="174" width="82" height="16" rx="3"/><rect x="642" y="174" width="62" height="16" rx="3" fill="#8fa2a0"/><rect x="858" y="168" width="100" height="28" rx="3" fill="#4a4f55"/>
      <rect x="163" y="240" width="76" height="24" rx="3" fill="#4a4f55"/><rect x="412" y="238" width="50" height="28" rx="3" fill="#c94a4a"/><rect x="600" y="236" width="146" height="32" rx="4" fill="#2fae6a"/><rect x="860" y="238" width="98" height="28" rx="3" fill="#d33a2c"/>
      <rect x="170" y="311" width="62" height="22" rx="3" fill="#7ab648"/><rect x="402" y="308" width="70" height="28" rx="3" fill="#6b7076"/><rect x="616" y="308" width="116" height="28" rx="3" fill="#2f6fb5"/><rect x="875" y="310" width="66" height="24" rx="3" fill="#5f6b6f"/>
      <rect x="170" y="381" width="64" height="24" rx="3" fill="#6aa6d9"/><rect x="392" y="384" width="90" height="18" rx="3" fill="#3a6a9a"/><rect x="648" y="386" width="50" height="14" rx="3"/><rect x="862" y="378" width="96" height="28" rx="3" fill="#2d5ca8"/>
      <rect x="170" y="451" width="64" height="26" rx="3" fill="#2a5aa8"/><rect x="406" y="456" width="60" height="16" rx="3" fill="#3a4f7a"/><rect x="636" y="451" width="78" height="26" rx="3" fill="#d94a3a"/><rect x="874" y="456" width="70" height="16" rx="3"/>
      <rect x="150" y="522" width="104" height="28" rx="3" fill="#3d86c9"/><rect x="416" y="520" width="40" height="30" rx="3" fill="#7c4ab3"/><rect x="633" y="522" width="76" height="26" rx="3" fill="#d82a2a"/>
    </g>
  </svg>
  <div class="footer-url">www.travolin.com.au</div>
  <div class="footer-page">Page: <b>5</b></div>
</section>

<!-- Slide 6: closing -->
<section class="slide s6">
  <svg class="hero" width="1112" height="460" viewBox="0 0 1112 460" role="img" aria-label="Photo of glowing programming code on a dark blue screen">
    <defs>
      <linearGradient id="codeGlow" x1="0" y1="0" x2="1" y2="0">
        <stop offset="0" stop-color="#061a33"/>
        <stop offset=".4" stop-color="#0d3a66"/>
        <stop offset=".75" stop-color="#145a8a"/>
        <stop offset="1" stop-color="#2aa6c9"/>
      </linearGradient>
    </defs>
    <path d="M0 318 C300 490 820 420 1112 175 V195 C820 445 300 510 0 338 Z" fill="var(--sky-deep)"/>
    <path d="M0 0 H1112 V160 C820 410 300 470 0 300 Z" fill="url(#codeGlow)"/>
  </svg>
  <div class="brand cover-brand" style="top:503px">travolin</div>
  <div class="divider" style="left:398px;top:505px;height:90px"></div>
  <div class="thanks">THANK YOU</div>
  <div class="site">
    <svg width="18" height="18" viewBox="0 0 18 18" aria-hidden="true"><circle cx="9" cy="9" r="8" fill="var(--sky)"/><ellipse cx="9" cy="9" rx="3.5" ry="8" fill="none" stroke="#fff" stroke-width="1.2"/><line x1="1" y1="9" x2="17" y2="9" stroke="#fff" stroke-width="1.2"/></svg>
    <span>www.travolin.com.au</span>
  </div>
</section>

</body>
</html>
```